Business card design for holistic health care clinic

We need a double-sided business card design for our holistic health care clinic that integrates our logo design and also its color scheme. My business is called Valmira. It is an integrative medicine clinic. You have already done the logo for me. Please ensure an elegant and upscale design that is not cluttered, but still has all the necessary information (please see below for details).

Target Market(s)

Wellness, fitness, rehabilitation for educated, well-traveled open-minded clients who are focused on natural, organic, balanced and preventive healthcare and lifestyle.

Industry/Entity Type

Medical

Contact Information for Business Card

Modern, clean.

Number of Pages Required

1 page

Font styles to use
Serif
Sans Serif

Colors

Designer to choose colors to be used in the design.

Requirements
Must have
• Logo on one side, all other information on the other side.
• Other information should include:
• Tobias Wrenfeld - DOE, CPT, LMT
• 4100 East Marrow Drive
• Austin, TX 78119
• 512 555 0148
• 818 555 0192
• info@ValmiraHealth.example
• t.wrenfeld@ValmiraHealth.example
Nice to have
• Darker background on front - but not totally black - shaded/dark gray.

```html
<!DOCTYPE html>
<html lang="en">
<head>
<meta charset="utf-8">
<title>Valmira – Business Card</title>
<link rel="stylesheet" href="https://fonts.googleapis.com/css2?family=Nunito:wght@800&family=Source+Sans+3:wght@400;600&display=swap">
<style>
  :root {
    --stage: #1f1f1f;
    --paper: #ffffff;
    --brand-blue: #0a90ce;
    --ink: #2b2b2b;
    --on-blue: #ffffff;
  }
  * { margin: 0; padding: 0; box-sizing: border-box; }
  html, body { width: 1200px; height: 900px; overflow: hidden; }
  body {
    background: var(--stage);
    font-family: "Source Sans 3", "Helvetica Neue", Arial, sans-serif;
    position: relative;
  }
  .card {
    position: absolute;
    top: 300px;
    width: 442px;
    height: 273px;
    border-radius: 10px;
    overflow: hidden;
  }
  .card--info { left: 152px; background: var(--paper); color: var(--ink); }
  .card--brand { left: 622px; background: var(--brand-blue); color: var(--on-blue); text-align: center; }

  .brand-name {
    font-family: "Nunito", "Arial Rounded MT Bold", sans-serif;
    font-weight: 800;
    letter-spacing: 1px;
    line-height: 1;
  }
  .brand-tagline {
    font-family: "Source Sans 3", Arial, sans-serif;
    font-weight: 600;
    line-height: 1;
    white-space: nowrap;
  }

  .card--info .lockup {
    position: absolute;
    right: 28px;
    top: 46px;
    width: 184px;
    text-align: center;
    color: var(--brand-blue);
  }
  .card--info .brand-name { font-size: 40px; }
  .card--info .brand-tagline { font-size: 13px; margin-top: 5px; }

  .holder { position: absolute; left: 27px; top: 161px; }
  .holder-name { font-size: 18px; color: var(--brand-blue); letter-spacing: 0.5px; line-height: 1; }
  .holder-credentials { font-size: 12px; margin-top: 6px; line-height: 1; }
  .address { margin-top: 19px; font-size: 12.5px; line-height: 17px; }

  .contacts {
    position: absolute;
    right: 22px;
    top: 182px;
    list-style: none;
    font-size: 12px;
    line-height: 16px;
    white-space: nowrap;
  }
  .contacts li { display: flex; align-items: center; gap: 6px; }
  .contacts svg { width: 9px; height: 9px; fill: var(--brand-blue); flex: none; }

  .card--brand .lockup { position: absolute; left: 0; right: 0; top: 112px; }
  .card--brand .brand-name { font-size: 66px; letter-spacing: 2px; }
  .card--brand .brand-tagline { font-size: 19px; margin-top: 4px; }
  .website { position: absolute; left: 0; right: 0; top: 222px; font-size: 12px; letter-spacing: 2px; }
</style>
</head>
<body>
  <section class="card card--info" aria-label="Business card, contact side">
    <div class="lockup">
      <div class="brand-name">VALMIRA</div>
      <div class="brand-tagline">Integrative Holistic Medicine</div>
    </div>

    <div class="holder">
      <p class="holder-name">TOBIAS WRENFELD</p>
      <p class="holder-credentials">DOE,CPT,LMT</p>
      <p class="address">4100 East Marrow Drive<br>Austin, TX 78119</p>
    </div>

    <ul class="contacts">
      <li><svg viewBox="0 0 10 10" aria-hidden="true"><path d="M3 0h4a1 1 0 0 1 1 1v8a1 1 0 0 1-1 1H3a1 1 0 0 1-1-1V1a1 1 0 0 1 1-1zm0 1.5v6h4v-6z"/></svg>512 555 0148</li>
      <li><svg viewBox="0 0 10 10" aria-hidden="true"><path d="M0 3.5C0 2 2 1 5 1s5 1 5 2.5V5H7.5V4h-5v1H0zM2 5.5h6l1 3.5H1z"/></svg>818 555 0192</li>
      <li><svg viewBox="0 0 10 10" aria-hidden="true"><path d="M0 2h10v6H0zm1 .8v.3l4 2.6 4-2.6v-.3z"/></svg>info@ValmiraHealth.example</li>
      <li><svg viewBox="0 0 10 10" aria-hidden="true"><path d="M0 2h10v6H0zm1 .8v.3l4 2.6 4-2.6v-.3z"/></svg>t.wrenfeld@ValmiraHealth.example</li>
    </ul>
  </section>

  <section class="card card--brand" aria-label="Business card, brand side">
    <div class="lockup">
      <div class="brand-name">VALMIRA</div>
      <div class="brand-tagline">Integrative Holistic Medicine</div>
    </div>
    <p class="website">www.ValmiraHealth.example</p>
  </section>
</body>
</html>
```